Website for Torvel Capital - investment banking firm

We have a corporate identity (thanks to Ravinka/31842) and want to extend that into a website design.  See the attached zipped files.
We have software folks in-house to do the coding.
See the attached Project Brief & Notes for more details.  Don't worry about the actual text - lorem ipsum will be fine.
The server will be Apache.
Thank you!
Desmond

Industry/Entity Type
Investment

```html
<!DOCTYPE html>
<html lang="en">
<head>
<meta charset="utf-8">
<title>Torvel Capital</title>
<link href="https://fonts.googleapis.com/css2?family=Cinzel:wght@500&family=Tinos:wght@400;700&family=Lato:ital,wght@0,400;0,700;1,400;1,700&display=swap" rel="stylesheet">
<style>
:root{
  --blue:#1f4f9c;
  --ink:#2b2b2b;
  --muted:#555;
  --band:#efefef;
  --card:#fff;
  --line:#d9d9d9;
  --btn:#777;
  --footer:#333;
  --footer-bottom:#262626;
  --tick:#6aa84f;
}
*{box-sizing:border-box;margin:0;padding:0}
html,body{width:731px;height:1200px;overflow:hidden}
body{position:relative;font-family:'Lato',sans-serif;color:var(--ink);background:#fff;font-size:8px}
.abs{position:absolute}
.brand{font-family:'Cinzel',serif;color:var(--blue);letter-spacing:.5px}

/* header */
.logo{left:80px;top:16px;display:flex;align-items:center;gap:8px}
.logo .mark{width:30px;height:30px;background:var(--blue)}
.logo .divider{width:1px;height:40px;background:var(--blue)}
.logo .brand{font-size:20px}
.contact{right:80px;top:13px;font-size:7.5px}
.contact div{display:flex;align-items:center;gap:6px}
.contact .phone{margin-top:10px;font-size:11px;color:var(--blue);font-weight:700;letter-spacing:.5px}

/* nav */
.nav{left:0;top:70px;width:731px;height:33px;background:var(--blue)}
.nav ul{list-style:none;display:flex;position:absolute;left:80px;top:0;height:33px}
.nav li{color:#fff;font-size:9.5px;line-height:33px;padding:0 18px;border-right:1px solid rgba(255,255,255,.15)}
.nav li:last-child{border:none}
.nav li.active{background:#8a8f97}

/* hero */
.hero-band{left:0;top:103px;width:731px;height:257px;background:linear-gradient(#f4f4f4,#e9e9e9)}
.hero{left:80px;top:104px;width:571px;height:227px;background:#fff;border:1px solid #e2e2e2;overflow:hidden}
.hero-photo{right:0;top:0;width:300px;height:226px;background:radial-gradient(ellipse at 60% 45%,#e3d4c4 0,#efe9e2 40%,#fff 75%)}
.hero .brand{left:13px;top:50px;font-size:21px}
.hero h1{left:13px;top:78px;font-family:'Tinos',serif;font-size:19px;color:var(--blue);font-weight:700}
.hero p{left:13px;font-size:9px}
.cta{left:14px;top:147px;height:28px;background:#1d1d1d;color:#fff;font-size:11px;line-height:28px;padding:0 16px 0 10px}
.cta:after{content:"";position:absolute;right:-8px;top:0;border-left:8px solid #1d1d1d;border-top:14px solid transparent;border-bottom:14px solid transparent}

/* cards */
.card{top:384px;width:172px;height:198px;background:var(--card);border:1px solid #ddd;border-radius:3px;box-shadow:0 3px 5px rgba(0,0,0,.08)}
.card-head{position:absolute;left:-3px;top:4px;width:178px;height:25px;background:var(--blue);color:#fff;display:flex;align-items:center;gap:8px;padding-left:6px}
.card-head .sq{width:16px;height:16px;background:#9aa3b0}
.card-head h2{font-family:'Tinos',serif;font-weight:400;font-size:14px}
.card-photo{position:absolute;left:7px;top:34px;width:158px;height:78px}
.card-text{position:absolute;left:7px;top:118px;width:160px;font-size:7.5px;line-height:12px;color:var(--muted)}
.card-list{position:absolute;left:7px;top:118px;list-style:none;font-size:7.2px;font-weight:700;color:#444}
.card-list li{padding-left:10px;position:relative;margin-bottom:5px;line-height:10.5px}
.card-list li:before{content:"";position:absolute;left:0;top:2px;border-left:4px solid #888;border-top:3px solid transparent;border-bottom:3px solid transparent}
.more{position:absolute;left:10px;top:185px;background:var(--btn);color:#fff;font-size:8px;padding:3px 7px}

/* testimonials / news */
.mid-band{left:0;top:609px;width:731px;height:219px;background:var(--band)}
.sec-title{font-family:'Tinos',serif;font-weight:400;font-size:14px;color:#333}
.sec-title span{color:var(--blue)}
.rule{height:1px;background:var(--line)}
.quote{left:80px;top:664px;width:268px;height:93px;background:#f8f8f8;padding:8px 9px;font-style:italic;font-size:7px;line-height:13.5px;color:#444}
.quote b{font-size:8.5px;color:#222}
.avatar{left:94px;top:766px;width:50px;height:50px;border-radius:50%;background:#c8ccd2;border:3px solid #fff;box-shadow:0 0 0 1px #ccc}
.cite{left:158px;top:793px;font-size:10px;color:var(--blue)}
.news h3{font-weight:400;font-size:11.5px;color:#333}
.news .date{font-size:7.5px;color:var(--blue);font-weight:700;margin:5px 0 4px}
.news p{font-size:7.3px;line-height:12px;color:#444;margin-bottom:7px}
.news .btn{display:inline-block;background:#222;color:#fff;font-size:6.5px;padding:4px 6px;margin-top:3px}

/* acquisition */
.acq{left:80px;top:845px;width:571px;height:122px;border:1px solid #ddd;border-radius:3px;background:#fff}
.acq h2{position:absolute;left:12px;top:9px;font-family:'Tinos',serif;font-weight:400;font-size:15px;color:#777}
.acq h2 span{color:var(--blue)}
.acq p{position:absolute;left:12px;top:33px;font-size:7.8px;color:#555}
.acq .cols{position:absolute;left:16px;top:55px;display:flex}
.acq ul{list-style:none;width:136px;border-right:1px solid #e3e3e3}
.acq ul:not(:first-child){padding-left:18px}
.acq ul:last-child{border:none}
.acq li{font-size:8px;color:#555;height:18.5px;display:flex;align-items:center;gap:6px}

/* partner names */
.partners{left:80px;top:983px;width:571px;height:36px;display:flex;justify-content:space-around;align-items:center}
.partners span{font-weight:700;font-size:18px;color:#666;display:flex;align-items:center;gap:6px}
.partners i{width:10px;height:10px;border-radius:50%;background:#888;display:inline-block}

/* footer */
.footer{left:0;top:1032px;width:731px;height:148px;background:var(--footer);color:#ddd}
.f-col{position:absolute;top:15px}
.f-col h4{font-weight:400;font-size:10.5px;color:#eee;padding-bottom:6px;border-bottom:1px solid #4a4a4a;margin-bottom:6px}
.f-links li{list-style:none;font-size:7.5px;line-height:17px}
.f-links li:before{content:"› "}
.map{width:143px;height:86px;background:linear-gradient(135deg,#d9dde2,#c7ccd3);border:2px solid #fff}
.f-addr li{list-style:none;font-size:7px;line-height:11px;padding-left:18px;position:relative;margin-bottom:3px}
.f-addr svg{position:absolute;left:0;top:1px}
.social{width:74px;height:22px;border:1px solid #555;font-size:7px;display:flex;align-items:center;gap:10px;padding-left:10px;margin-bottom:7px}
.social i{width:9px;height:9px;background:#ddd;display:inline-block}
.copy{left:0;top:1180px;width:731px;height:20px;background:var(--footer-bottom);color:#ccc;font-size:7px;text-align:center;line-height:20px}
</style>
</head>
<body>

<header>
  <div class="abs logo"><div class="mark"></div><div class="divider"></div><div class="brand">TORVEL CAPITAL</div></div>
  <div class="abs contact">
    <div><svg width="12" height="9" viewBox="0 0 12 9"><rect width="12" height="9" rx="1" fill="#333"/><path d="M1 1l5 4 5-4" stroke="#fff" fill="none"/></svg>info@torvelcapital.com</div>
    <div class="phone"><svg width="12" height="12" viewBox="0 0 12 12"><rect width="12" height="12" rx="2" fill="#333"/><rect x="4" y="2" width="4" height="8" rx="1" fill="#fff"/></svg>555-210-4836</div>
  </div>
</header>

<nav class="abs nav"><ul>
  <li class="active">Home</li><li>About</li><li>Services</li><li>Current Engagements</li><li>Completed Transactions</li><li>Contact Us</li>
</ul></nav>

<section>
  <div class="abs hero-band"></div>
  <div class="abs hero">
    <div class="abs hero-photo" role="img" aria-label="Cupped hands sheltering a seedling growing from a pile of coins"></div>
    <div class="abs brand">TORVEL CAPITAL</div>
    <h1 class="abs">Private Investment Banking</h1>
    <p class="abs" style="top:105px">advisory firm that acts as an intermediary on behalf of</p>
    <p class="abs" style="top:124px;font-size:10.5px;letter-spacing:.4px">BUYERS &amp; SELLERS OF PRIVATE COMPANIES.</p>
    <div class="abs cta">Get Started Now</div>
  </div>
</section>

<section>
  <article class="abs card" style="left:83px">
    <div class="card-head"><div class="sq"></div><h2>Who We Are</h2></div>
    <div class="card-photo" role="img" aria-label="Group of smiling business professionals" style="background:linear-gradient(#e6e8eb,#b9a98f)"></div>
    <p class="card-text">Torvel Capital's history in mergers and acquisitions traces back to 1998. We pride our selves in successfully matching buyers with sellers and enabling shareholders of all stakeholders in a transaction to prosper.</p>
    <span class="more">Read More</span>
  </article>
  <article class="abs card" style="left:280px">
    <div class="card-head"><div class="sq"></div><h2>What We Do</h2></div>
    <div class="card-photo" role="img" aria-label="Business team meeting around a table" style="background:linear-gradient(#dfe3e8,#6f7c8c)"></div>
    <ul class="card-list"><li>Buy-Side Acquisitions</li><li>Recapitalizations &amp; Growth Capital<br>Partnerships</li><li>Sell-Side Transactions</li></ul>
    <span class="more">Read More</span>
  </article>
  <article class="abs card" style="left:477px">
    <div class="card-head"><div class="sq"></div><h2>Deal Structure</h2></div>
    <div class="card-photo" role="img" aria-label="Handshake over a desk" style="background:linear-gradient(120deg,#6a8fb8,#d8dde4)"></div>
    <p class="card-text">Successful completion of a transaction requires agreement on much more than transfer price. We evaluate key factors such as the amount of consideration to be paid, timing of payments, transfer of obligations,</p>
    <span class="more">Read More</span>
  </article>
</section>

<section>
  <div class="abs mid-band"></div>
  <h2 class="abs sec-title" style="left:80px;top:629px">Client <span>Testimonials</span></h2>
  <div class="abs" style="left:322px;top:632px"><svg width="25" height="12" viewBox="0 0 25 12"><circle cx="6" cy="6" r="5.3" fill="none" stroke="#888"/><path d="M7 3.5L4.5 6 7 8.5" stroke="#888" fill="none"/><circle cx="19" cy="6" r="5.3" fill="none" stroke="#888"/><path d="M18 3.5L20.5 6 18 8.5" stroke="#888" fill="none"/></svg></div>
  <div class="abs rule" style="left:80px;top:652px;width:268px"></div>
  <blockquote class="abs quote"><b>“ Lorem ipsum dolor sit amet, consectetuer adipiscing elit</b><br>Sed diam nonummy nibh euismod tiidunt ut laoreet dolore magna aliqm erat volutpat Ut wisi enim ad minim veniam, quis nostrud exeon ullcoper suscipit lobortis nis volpat.Ut wisi enim ad minim veniam, quis nostrud exerci tation ullcoper suscipit lobortis nis volpat.Ut wisi enim ad minim iam, quis nostrud exerci tation ullcoper suscipit lobortis nis volpat.</blockquote>
  <div class="abs avatar" role="img" aria-label="Client portrait"></div>
  <div class="abs cite">— Marlon Fescue</div>

  <h2 class="abs sec-title" style="left:382px;top:629px">Latest <span>News</span></h2>
  <div class="abs" style="left:625px;top:632px"><svg width="25" height="12" viewBox="0 0 25 12"><circle cx="6" cy="6" r="5.3" fill="none" stroke="#444"/><path d="M7 3.5L4.5 6 7 8.5" stroke="#444" fill="none"/><circle cx="19" cy="6" r="5.3" fill="none" stroke="#444"/><path d="M18 3.5L20.5 6 18 8.5" stroke="#444" fill="none"/></svg></div>
  <div class="abs rule" style="left:382px;top:652px;width:268px"></div>
  <div class="abs news" style="left:382px;top:661px;width:270px">
    <h3>Lorem ipsum dolor sit amet constetuer adipiscing elit</h3>
    <div class="date">January 8, 2014</div>
    <p>Sed diam nonummy nibod tiidunt ut laoreet dolore magna aliqam erat voluati ug wisi enim ad minim veniam, quis nostrud exerci tation upr suscipit lobortisl nis volpat.Ut wisi enim ad minim veniam, quis nostrud.</p>
    <p>Ut wisi enim ad minim veniamuis nostrud exerci tation ullcoper supit lobortisl nis volpat.Ut wisi enim ad minim veniamuis nostrud exerci tation per suscipitl lobortis nis volpat. wisi enim ad minim veniam, qunrud exerci tation ullcopery suscipit lobortis nis volpat.Ut wisi enim ad minim veniam,</p>
    <span class="btn">READ MORE »</span>
  </div>
</section>

<section class="abs acq">
  <h2><span>Current Acquisition</span> Search Info</h2>
  <p>The following is a list of recent searches. Current search criteria is extensive. Please contact us for more information.</p>
  <div class="cols">
    <ul><li><svg width="10" height="9" viewBox="0 0 10 9"><path d="M1 5l3 3 5-7" stroke="#6aa84f" stroke-width="2" fill="none"/></svg>Oilfield Services</li><li><svg width="10" height="9" viewBox="0 0 10 9"><path d="M1 5l3 3 5-7" stroke="#6aa84f" stroke-width="2" fill="none"/></svg>Oilfield Manufacturing</li><li><svg width="10" height="9" viewBox="0 0 10 9"><path d="M1 5l3 3 5-7" stroke="#6aa84f" stroke-width="2" fill="none"/></svg>Asset Managment</li></ul>
    <ul><li><svg width="10" height="9" viewBox="0 0 10 9"><path d="M1 5l3 3 5-7" stroke="#6aa84f" stroke-width="2" fill="none"/></svg>Insurance Brokerage</li><li><svg width="10" height="9" viewBox="0 0 10 9"><path d="M1 5l3 3 5-7" stroke="#6aa84f" stroke-width="2" fill="none"/></svg>3PL / Logistics</li><li><svg width="10" height="9" viewBox="0 0 10 9"><path d="M1 5l3 3 5-7" stroke="#6aa84f" stroke-width="2" fill="none"/></svg>Special Situations</li></ul>
    <ul><li><svg width="10" height="9" viewBox="0 0 10 9"><path d="M1 5l3 3 5-7" stroke="#6aa84f" stroke-width="2" fill="none"/></svg>Food Manufacturers</li><li><svg width="10" height="9" viewBox="0 0 10 9"><path d="M1 5l3 3 5-7" stroke="#6aa84f" stroke-width="2" fill="none"/></svg>Insurance MGA's</li><li><svg width="10" height="9" viewBox="0 0 10 9"><path d="M1 5l3 3 5-7" stroke="#6aa84f" stroke-width="2" fill="none"/></svg>Healthcare Providers</li></ul>
    <ul><li><svg width="10" height="9" viewBox="0 0 10 9"><path d="M1 5l3 3 5-7" stroke="#6aa84f" stroke-width="2" fill="none"/></svg>Medical Instrumentation</li><li><svg width="10" height="9" viewBox="0 0 10 9"><path d="M1 5l3 3 5-7" stroke="#6aa84f" stroke-width="2" fill="none"/></svg>Metals and Materials</li><li><svg width="10" height="9" viewBox="0 0 10 9"><path d="M1 5l3 3 5-7" stroke="#6aa84f" stroke-width="2" fill="none"/></svg>Industrial Products/Services</li></ul>
  </div>
</section>

<section class="abs partners">
  <span>Kestrel</span><span><i></i>Norvane</span><span>Lumfield</span><span><i></i>Orison</span><span>Hollowmere</span>
</section>

<footer class="abs footer">
  <div class="f-col" style="left:86px;width:95px"><h4>Quick Links</h4>
    <ul class="f-links"><li>Home</li><li>About Us</li><li>Services</li><li>Current Engagements</li><li>Completed Transactions</li><li>Contact Us</li></ul></div>
  <div class="f-col" style="left:217px;width:145px"><h4 style="border:none">Location Map</h4>
    <div class="map" role="img" aria-label="Street map showing office location"></div></div>
  <div class="f-col" style="left:393px;width:160px"><h4>Client Testimonials</h4>
    <ul class="f-addr">
      <li><svg width="8" height="10" viewBox="0 0 8 10"><path d="M4 10L1 5a3 3 0 1 1 6 0z" fill="#ddd"/></svg>Hong Kong: Room 1804 Harbour Crest<br>12 Lantern Road<br>Kowloon, Hong Kong</li>
      <li><svg width="8" height="10" viewBox="0 0 8 10"><path d="M4 10L1 5a3 3 0 1 1 6 0z" fill="#ddd"/></svg>Arlington: 1400 Meridian Way, Suite 220</li>
      <li><svg width="10" height="9" viewBox="0 0 10 9"><rect y="3" width="10" height="4" fill="#ddd"/><rect x="2" width="6" height="3" fill="#ddd"/></svg>Arlington, Texas 76011</li>
      <li><svg width="9" height="9" viewBox="0 0 9 9"><path d="M1 1h2l1 2-1 1a5 5 0 0 0 2 2l1-1 2 1v2c-4 0-8-4-8-7z" fill="#ddd"/></svg>Telephone: 555-210-4836</li>
      <li><svg width="10" height="8" viewBox="0 0 10 8"><rect width="10" height="8" fill="#ddd"/><path d="M1 1l4 3 4-3" stroke="#333" fill="none"/></svg>E-mail: info@torvelcapital.com</li>
    </ul></div>
  <div class="f-col" style="left:576px;width:76px"><h4>Follow Us</h4>
    <div class="social"><i></i>Linkmere</div><div class="social"><i></i>Circleway</div><div class="social"><i></i>Postly</div></div>
</footer>
<div class="abs copy">© Copyright 2014 Torvel Capital. | All Rights Reserved</div>

</body>
</html>
```